BRIGHT RIVER POWER.

I'd like my business logo.
contact name: Dennis Halvorsen
phone:0438759164
email: info@brightriverpower.net.au
website: www.brightriverpower.net.au

services:
solar
battery storage
LED lighting
energy saving solutions
general electrical
I'd like the design to look professional

Target Market(s)

Everyone

Industry/Entity Type

Business

Contact Information for Business Card

as described above

Requirements
Must have
• Id like the colours and the design to work well with my logo.

```html
<!DOCTYPE html>
<html lang="en">
<head>
<meta charset="utf-8">
<title>Bright River Power – Business Card</title>
<link href="https://fonts.googleapis.com/css2?family=Source+Sans+3:wght@400;600;700&display=swap" rel="stylesheet">
<style>
  :root {
    --backdrop-top: #2a2a2a;
    --backdrop-bottom: #050505;
    --card-front: #f3f3f3;
    --card-back: #4fb57c;
    --brand-green: #4caf6e;
    --brand-orange: #f5a623;
    --soft-green: #8fd3a6;
    --ink: #2b2b2b;
    --white: #ffffff;
  }
  * { margin: 0; padding: 0; box-sizing: border-box; }
  html, body {
    width: 1200px;
    height: 900px;
    overflow: hidden;
  }
  body {
    position: relative;
    background: radial-gradient(ellipse at 50% 10%, var(--backdrop-top) 0%, #151515 55%, var(--backdrop-bottom) 100%);
    font-family: "Source Sans 3", "Myriad Pro", Arial, sans-serif;
  }
  .card {
    position: absolute;
    top: 184px;
    height: 490px;
    border-radius: 14px;
    text-align: center;
  }
  .card--front {
    left: 299px;
    width: 301px;
    background: var(--card-front);
  }
  .card--back {
    left: 645px;
    width: 304px;
    background: var(--card-back);
    color: var(--white);
  }
  .brand {
    position: absolute;
    top: 88px;
    left: 0;
    right: 0;
    display: flex;
    flex-direction: column;
    align-items: center;
  }
  .brand__dot {
    width: 62px;
    height: 62px;
    border-radius: 50%;
    background: var(--brand-orange);
  }
  .brand__name {
    margin-top: 44px;
    font-size: 24px;
    font-weight: 700;
    letter-spacing: 0.5px;
    color: var(--brand-green);
  }
  .contact-name {
    position: absolute;
    top: 308px;
    left: 0;
    right: 0;
    font-size: 17px;
    font-weight: 600;
    color: var(--brand-green);
  }
  .contact-list {
    position: absolute;
    top: 352px;
    left: 0;
    right: 0;
    list-style: none;
    font-size: 13.5px;
    line-height: 17.5px;
    color: var(--ink);
  }
  .back-emblem {
    position: absolute;
    top: 100px;
    left: 92px;
    width: 120px;
    height: 120px;
    border-radius: 50%;
    background: var(--soft-green);
  }
  .services__title {
    position: absolute;
    top: 348px;
    left: 0;
    right: 0;
    font-size: 15px;
    font-weight: 600;
  }
  .services__list {
    position: absolute;
    top: 382px;
    left: 0;
    right: 0;
    list-style: none;
    font-size: 14px;
    line-height: 18px;
  }
</style>
</head>
<body>
  <section class="card card--front">
    <div class="brand">
      <span class="brand__dot"></span>
      <span class="brand__name">BRIGHT RIVER POWER</span>
    </div>
    <p class="contact-name">Dennis Halvorsen</p>
    <ul class="contact-list">
      <li>0438759164</li>
      <li>info@brightriverpower.net.au</li>
      <li>www.brightriverpower.net.au</li>
    </ul>
  </section>

  <section class="card card--back">
    <span class="back-emblem"></span>
    <h2 class="services__title">WHAT I DO</h2>
    <ul class="services__list">
      <li>Solar | Battery Storage</li>
      <li>LED Lighting | Energy Saving Solutions</li>
    </ul>
  </section>
</body>
</html>
```